A website where experts collaborate on your project

I am building a new website where experts (yes, like designers) collaborate on projects with the project owner. More minds = more collaboration = better end product. Please see Pelmora(dot)com for a quick landing page I created for collaborating on presentations (although there will be many project types offered)

I am looking for a DESIGNER LONG TERM, but for now, just need initial mock ups to show the web programmers.

I have 21 Word documents loosely designed, what I would like to see here is a theme. Please DO NOT GO OFF WHAT YOU CURRENTLY SEE AT PELMORA. What is up now is only a quick landing page.

You can view a Word doc of the homepage here:
https://www.filevanta.com/s/qx83kdm2/home.docx?dl=0

WHAT AM I LOOKING FOR?
A clean, well designed theme.

Here is a link to the logo:
https://www.filevanta.com/s/mr47tpz9/logo%20-%20horizontal.tif?dl=0
-----------------------------------------
Here are a few sites I like the design of and what I like about them:
www.quenbrook.com-all around my favorite, beautiful graphics, clean layout, bold use of colors on a dark background
Ravelto.com- clean layout, The use of humans and bubble style elements.
Mintharbor.com :) clean, bold, unique pop art style but professional
plumevault.com - From the unique colors and artwork and the ability of that art to not interfere with the important elements of the site
sparkwidgets.com-clean, nice colors, well organized and separated sections.
www.dunmereco.com-love the font, use of colors and sectionalized style

All in all, I am not picky and open to so many styles. I would ultimately like the designer I pick to design all 21 pages.
Updates

Hello everyone,Moving forward, I would like you all to pay special attention to the section in my brief titled "Here are a few sites I like the design of and what I like about them". Please see below, I handpicked each one of these as sites I really like. Thank you.Here are a few sites I like the design of and what I like about them:Ravelto.com- clean layout, The use of humans and bubble style elements.Mintharbor.com :) clean, bold, unique pop art style but professionalwriteraccess.com - From the unique colors and artwork and the ability of that art to not interfere with the important elements of the sitegrowthgeeks.com-clean, nice colors, well organized and separated sections.www.dunmereco.com-love the font, use of colors and sectionalized stylewww.quenbrook.com-beautiful graphics, clean layout, bold use of colors----------------------------------------- Added Tuesday, November 24, 2015

I updated the homepage, you can see it here:https://www.dropbox.com/s/kwlkbsookq3cg2m/1new%20homepage.docx?dl=0I am modeling it after my favorite designed site: triplelift.comI love the dark colors with the orange glowing style boldness of the buttons. It's real clean too. Added Tuesday, November 24, 2015

Target Market(s)

small business owners, marketers, freelancer writers, graphic designers,

Industry/Entity Type

Building

Number of Pages Required

5+ page

Requirements
Must have
• I can't think of anything the project must have.
Nice to have
• WHAT AM I LOOKING FOR?
• A clean, well designed theme. I had a designer do a bit of work putting elements together, I found it to be very plain, but I like the Application Page (https://www.filevanta.com/s/jb19ckr3/Pelmora-Website.ai?dl=0)
• Here is a link to the logo:
• https://www.filevanta.com/s/mr47tpz9/logo%20-%20horizontal.tif?dl=0
• Here are a few sites I like the design of and what I like about them:
• Ravelto.com- clean layout, The use of humans and bubble style elements.
• Mintharbor.com :) clean, bold, unique pop art style but professional
• plumevault.com - From the unique colors and artwork and the ability of that art to not interfere with the important elements of the site
• sparkwidgets.com-clean, nice colors, well organized and separated sections.
• www.dunmereco.com-love the font, use of colors and sectionalized style
• www.quenbrook.com-beautiful graphics, clean layout, bold use of colors
• -----------------------------------------
Should not have
• out of the boxed, templated style website. I want this site to be memorable and not look like a thousand others

```html
<!DOCTYPE html>
<html lang="en">
<head>
<meta charset="utf-8">
<title>Pelmora – Crowd Projects</title>
<link href="https://fonts.googleapis.com/css2?family=Roboto:ital,wght@0,400;0,500;0,700;1,400&family=Roboto+Condensed:wght@400;700&display=swap" rel="stylesheet">
<style>
:root{
  --teal:#4aa9c6;
  --teal-dark:#2f8aa6;
  --orange:#f29322;
  --orange-deep:#e9861a;
  --ink:#2b2b2b;
  --muted:#555;
  --panel-bg:#ececec;
  --line:#dcdcdc;
  --card-grey:#e6e6e6;
  --footer:#262626;
  --white:#fff;
}
*{box-sizing:border-box;margin:0;padding:0}
html,body{width:776px;height:1200px;overflow:hidden}
body{font-family:"Roboto",sans-serif;color:var(--ink);background:var(--white);position:relative}
.abs{position:absolute}

/* top bar */
.topbar{left:0;top:0;width:776px;height:40px;background:var(--teal)}
.browse{left:57px;top:7px;width:131px;height:27px;background:var(--white);border:1px solid #cfd8dc;font-size:9px;color:#444;padding:7px 9px}
.caret{position:absolute;right:9px;top:11px;width:0;height:0;border-left:4px solid transparent;border-right:4px solid transparent;border-top:4px solid #333}
.call{right:57px;top:13px;font-size:12px;color:var(--white);font-weight:500}

/* header */
.header{left:0;top:40px;width:776px;height:80px;background:var(--white);border-bottom:1px solid #ddd}
.brand{left:59px;top:58px;display:flex;align-items:center;gap:8px}
.brand-name{font-size:20px;font-weight:500;color:var(--teal-dark)}
.brand-dot{width:28px;height:28px;border-radius:50%;background:var(--orange)}
.nav{top:80px;font-size:10px;color:#333;font-weight:500;letter-spacing:.2px}
.btn-notify{left:613px;top:68px;width:106px;height:30px;background:var(--orange);color:var(--white);font-size:10px;font-weight:500;display:flex;align-items:center;justify-content:center;letter-spacing:.3px}

/* hero */
.hero{left:0;top:120px;width:776px;height:360px;background:linear-gradient(90deg,#efefef 0%,#e7e8e9 30%,#b9c4cc 48%,#6f8395 62%,#d7b79b 82%,#c8a484 100%)}
.hero-title{left:55px;top:228px;font-family:"Roboto Condensed",sans-serif;font-size:27px;color:var(--orange-deep);letter-spacing:.2px}
.hero-sub{left:56px;top:264px;font-size:17.5px;line-height:22px;color:#333;letter-spacing:.3px}
.btn-start{left:56px;top:326px;width:133px;height:41px;background:linear-gradient(#3fa4c2,#2e8fae);color:var(--white);font-size:15px;font-weight:500;display:flex;align-items:center;justify-content:center;letter-spacing:.3px}

/* listing band */
.band{left:0;top:480px;width:776px;height:470px;background:var(--panel-bg)}
.filters{left:55px;top:519px;width:224px;height:409px;background:var(--white);box-shadow:0 1px 3px rgba(0,0,0,.15)}
.filters-head{position:absolute;left:0;top:0;width:224px;height:40px;background:linear-gradient(#55b3cf,#3d9dbb);color:var(--white);font-size:12px;font-weight:500;display:flex;align-items:center;justify-content:center;letter-spacing:.3px}
.price-title{position:absolute;left:0;top:62px;width:224px;text-align:center;font-size:10.5px;font-weight:500;letter-spacing:.2px}
.track{position:absolute;left:30px;top:92px;width:150px;height:5px;border-radius:3px;background:#c9c9c9}
.track-fill{position:absolute;left:40px;top:92px;width:93px;height:5px;background:#1f8fe0}
.knob{position:absolute;top:88px;width:8px;height:12px;border-radius:3px;background:#2f94dc;border:1px solid #1d6fb0}
.price-lbl{position:absolute;top:107px;font-size:7px;color:#333}
.filter-row{position:absolute;left:0;width:224px;height:39px;border-top:1px solid var(--line);font-size:9.5px;color:#333;padding:14px 0 0 20px;letter-spacing:.2px}
.filter-row::after{content:"";position:absolute;right:22px;top:15px;border-top:4px solid transparent;border-bottom:4px solid transparent;border-left:5px solid #333}

.sortbar{left:290px;top:519px;width:429px;height:51px;background:var(--white);box-shadow:0 1px 3px rgba(0,0,0,.15)}
.sortbar .label{position:absolute;left:16px;top:21px;font-size:9.5px;letter-spacing:.2px}
.sortbar .sort{position:absolute;left:158px;top:21px;font-size:9.5px}
.select{position:absolute;top:15px;width:73px;height:21px;border:1px solid #ccc;font-size:8.5px;color:#444;padding:5px 7px}
.select .caret{top:8px;right:7px}

.list{left:290px;top:579px;width:429px;height:349px;background:var(--white);box-shadow:0 1px 3px rgba(0,0,0,.15)}
.card{position:absolute;left:9px;width:411px;height:105px;background:var(--card-grey);box-shadow:0 1px 2px rgba(0,0,0,.12)}
.card.featured{background:var(--orange)}
.thumb{position:absolute;left:0;top:0;width:96px;height:105px;background:radial-gradient(circle at 50% 50%,#ffffff 30%,#e2e2e2 100%)}
.card-body{position:absolute;left:107px;top:10px;width:295px}
.card-title{font-size:10.5px;font-weight:500;line-height:16px}
.card-text{font-size:6.4px;line-height:12px;margin-top:5px;color:#555}
.card-more{font-size:6.8px;font-style:italic;text-decoration:underline;color:var(--orange-deep);margin-top:5px;display:block}
.featured .card-title,.featured .card-text,.featured .card-more{color:var(--white)}
.view-more{right:57px;top:934px;font-size:7.5px;font-weight:500;color:var(--teal-dark)}

/* testimonial */
.testimonial{left:0;top:950px;width:776px;height:177px;background:linear-gradient(180deg,#3c8ea5 0%,#2d7a91 55%,#2a6f85 100%)}
.t-title{left:0;top:975px;width:776px;text-align:center;font-size:18px;color:var(--white);letter-spacing:.5px}
.t-arrow{top:982px;width:8px;height:8px;border-top:1.5px solid var(--white);border-left:1.5px solid var(--white)}
.t-text{left:100px;top:1016px;width:576px;text-align:center;font-size:9.5px;line-height:16px;color:var(--white)}
.t-author{left:0;top:1077px;width:776px;text-align:center;font-size:10.5px;font-style:italic;color:var(--white)}

/* footer */
.footer{left:0;top:1127px;width:776px;height:73px;background:var(--footer)}
.f-links{left:57px;top:1147px;font-size:9px;color:#eee;word-spacing:1px}
.f-copy{left:58px;top:1166px;font-size:7.5px;color:#ddd}
.social{top:1150px;width:22px;height:22px}
</style>
</head>
<body>

<div class="abs topbar"></div>
<div class="abs browse">Browse<span class="caret"></span></div>
<div class="abs call">CALL US : 555-214-7730</div>

<div class="abs header"></div>
<div class="abs brand"><span class="brand-name">pelmora</span><span class="brand-dot"></span></div>
<div class="abs nav" style="left:299px">PROJECTS</div>
<div class="abs nav" style="left:374px">HOW IT WORKS</div>
<div class="abs nav" style="left:473px">PLANS</div>
<div class="abs nav" style="left:532px">MY ACCOUNT</div>
<div class="abs btn-notify">NOTIFICATION</div>

<div class="abs hero" role="img" aria-label="Photo of two smiling colleagues reviewing a document together at a desk"></div>
<div class="abs hero-title">CONVERT MORE CUSTOMERS</div>
<div class="abs hero-sub">Experience the power of experts<br>collaborating on your project.</div>
<div class="abs btn-start">GET STARTED</div>

<div class="abs band"></div>

<div class="abs filters">
  <div class="filters-head">FILTERS</div>
  <div class="price-title">SELECT YOUR PRICE RANGE</div>
  <div class="track"></div>
  <div class="track-fill"></div>
  <div class="knob" style="left:96px"></div>
  <div class="knob" style="left:189px"></div>
  <div class="price-lbl" style="left:91px">$100</div>
  <div class="price-lbl" style="left:184px">$800</div>
  <div class="filter-row" style="top:136px">COUNTRY</div>
  <div class="filter-row" style="top:175px">CATEGORIES</div>
  <div class="filter-row" style="top:214px">TIME LEFT</div>
  <div class="filter-row" style="top:253px">ACTIVE | EXPIRED</div>
  <div class="filter-row" style="top:292px">CONTAINS ADULT CONTENT</div>
  <div class="filter-row" style="top:331px">KEYWORDS</div>
  <div class="filter-row" style="top:370px">FOLLOWERS</div>
</div>

<div class="abs sortbar">
  <span class="label">CROWD PROJECTS:</span>
  <span class="sort">Sort:</span>
  <div class="select" style="left:184px">Price<span class="caret"></span></div>
  <div class="select" style="left:263px">country<span class="caret"></span></div>
  <div class="select" style="left:342px">Time left<span class="caret"></span></div>
</div>

<div class="abs list">
  <div class="card featured" style="top:10px">
    <div class="thumb" role="img" aria-label="Project thumbnail"></div>
    <div class="card-body">
      <div class="card-title">Morbi in ante arcu. Maecenas sit amet sem vel<br>$80, U.K., time left: 6 days</div>
      <div class="card-text">Lorem Ipsum has been the industry's standard dummy text ever since the 1500s, when an unknown printer took a galley of type and scrambled it to make a type specimen book. It has survived not only five centuries</div>
      <span class="card-more">View More</span>
    </div>
  </div>
  <div class="card" style="top:121px">
    <div class="thumb" role="img" aria-label="Project thumbnail"></div>
    <div class="card-body">
      <div class="card-title">Neque porro quisquam est qui dolorem ipsum<br>$250, U.S., time left: 6 days</div>
      <div class="card-text">Lorem Ipsum has been the industry's standard dummy text ever since the 1500s, when an unknown printer took a galley of type and scrambled it to make a type specimen book. It has survived not only five centuries</div>
      <span class="card-more">View More</span>
    </div>
  </div>
  <div class="card" style="top:232px">
    <div class="thumb" role="img" aria-label="Project thumbnail"></div>
    <div class="card-body">
      <div class="card-title">Duis ligula sapien, sodales id tortor vitae, ornare<br>$62, U.K., time left: 6 days</div>
      <div class="card-text">Lorem Ipsum has been the industry's standard dummy text ever since the 1500s, when an unknown printer took a galley of type and scrambled it to make a type specimen book. It has survived not only five centuries</div>
      <span class="card-more">View More</span>
    </div>
  </div>
</div>
<div class="abs view-more">View More &gt;&gt;</div>

<div class="abs testimonial" role="img" aria-label="Teal-tinted city skyline photo"></div>
<div class="abs t-arrow" style="left:302px;transform:rotate(-45deg)"></div>
<div class="abs t-title">TESTIMONIAL</div>
<div class="abs t-arrow" style="left:468px;transform:rotate(135deg)"></div>
<div class="abs t-text">Lorem Ipsum has been the industry's standard dummy text ever since the 1500s, when an unknown printer took a galley of type and scrambled it to make a type specimen book. It has survived not only five centuries, but also the leap into electronic typesetting, remaining essentially unchanged It was popularised in the 1960s with the release of Letraset sheets containing Lorem Ipsum passages</div>
<div class="abs t-author">Dana Whitfield, CEO, TBA</div>

<div class="abs footer"></div>
<div class="abs f-links">Privacy Policy &nbsp;|&nbsp; Terms of Use &nbsp;|&nbsp; About Us &nbsp;|&nbsp; Sitemap</div>
<div class="abs f-copy">Copyright © 2015 &nbsp;All Rights</div>
<div class="abs social" style="left:612px;background:#3fa9e0"></div>
<div class="abs social" style="left:641px;background:#d9342b"></div>
<div class="abs social" style="left:669px;background:#3b5a98"></div>
<div class="abs social" style="left:697px;background:#1f7ab8"></div>

</body>
</html>
```